Business Card Design - ChoiceCraft

Looking for creative, modern design, two sided for ChoiceCraft that is consistent with color and feel of website www.choicecraftpro.net.
Updates

Back of card will be used to promote products or have a quote revolving around decisions, change, leadership, innovation, creativity. Back should also have space to promote website, but optional to use the icon. Front of the card will need to use the icon and have standard place for name, job title, phone and email. We are not looking to put a mailing address or fax. Also want space to place a few words/phrase explaining what we do...such as individual growth and organizational development or tools, training, information...in addition, want the facebook icon small on the front somewhere as we are also on facebook.

Vector file uploaded of icon.

Target Market(s)

Professional coaching for individual growth and organizational development

Industry/Entity Type

Business

Requirements
Must have
• Icon...see attached.

```html
<!DOCTYPE html>
<html lang="en">
<head>
<meta charset="utf-8">
<title>ChoiceCraft Business Card</title>
<link rel="stylesheet" href="https://fonts.googleapis.com/css2?family=Arimo:wght@400;700&family=Tinos:wght@400;700&display=swap">
<style>
  :root {
    --stage: #b9bcc0;
    --card: #ffffff;
    --card-edge: #d4d6d9;
    --brand-blue: #2a8fd0;
    --quote-blue: #2b93d3;
    --navy: #2b3582;
    --band-start: #1c74c2;
    --band-end: #62c3f0;
    --ink: #222222;
    --ink-soft: #333333;
    --rule: #9a9a9a;
    --mark-fill: #6fa9d8;
  }
  * { box-sizing: border-box; margin: 0; padding: 0; }
  html, body { width: 1200px; height: 388px; overflow: hidden; }
  body { background: var(--stage); position: relative; font-family: "Tinos", "Times New Roman", serif; }

  .card {
    position: absolute; top: 36px; width: 544px; height: 311px;
    background: var(--card); border: 1px solid var(--card-edge); overflow: hidden;
  }
  .card--front { left: 35px; }
  .card--back { left: 617px; }

  /* Front */
  .brand { position: absolute; left: 115px; top: 24px; display: flex; align-items: center; }
  .brand__circle {
    width: 114px; height: 114px; border-radius: 50%;
    background: var(--mark-fill);
  }
  .brand__name {
    margin-left: 10px; font-weight: 700; font-size: 27px; color: var(--brand-blue);
    letter-spacing: 0.2px;
  }
  .identity { position: absolute; right: 238px; top: 182px; text-align: right; color: var(--ink); }
  .identity__name { font-size: 18px; font-weight: 700; }
  .identity__title { font-size: 14px; font-weight: 400; }
  .identity__tagline { margin-top: 14px; font-size: 14px; line-height: 19px; color: var(--ink-soft); }
  .divider { position: absolute; left: 311px; top: 187px; width: 1px; height: 72px; background: var(--rule); }
  .contact { position: absolute; left: 324px; top: 190px; list-style: none; font-size: 14px; color: var(--ink-soft); }
  .contact li { display: flex; align-items: center; height: 19.5px; }
  .contact svg { width: 11px; height: 11px; margin-right: 8px; fill: var(--ink-soft); flex: none; }
  .contact .social-square { width: 10px; height: 10px; margin-right: 9px; background: var(--navy); flex: none; }

  .band { position: absolute; left: 0; bottom: 0; width: 100%; height: 22px; }
  .band__light { position: absolute; inset: 0; background: linear-gradient(90deg, var(--band-start), var(--band-end) 55%); }
  .band__dark {
    position: absolute; top: 0; bottom: 0; left: 272px; right: 0; background: var(--navy);
    clip-path: polygon(22px 0, 100% 0, 100% 100%, 0 100%);
  }
  .band__url {
    position: absolute; left: 318px; top: 2px; font-size: 14.5px; letter-spacing: 1px; color: #ffffff;
  }

  /* Back */
  .quotes { position: absolute; left: 28px; top: 20px; list-style: none; font-family: "Arimo", Arial, sans-serif; }
  .quote { position: relative; height: 55px; padding-left: 50px; }
  .quote__dot { position: absolute; left: 1px; top: 6px; width: 22px; height: 22px; border-radius: 50%; background: var(--mark-fill); }
  .quote__text { font-size: 14px; color: var(--ink); line-height: 20px; position: relative; }
  .quote__text::before, .quote__text::after {
    font-family: "Tinos", serif; font-weight: 700; font-size: 28px; color: var(--ink); line-height: 0;
  }
  .quote__text::before { content: "\201C"; position: absolute; left: -18px; top: 14px; }
  .quote__text::after { content: "\201D"; position: relative; top: 12px; margin-left: 1px; }
  .quote__author { font-size: 14px; color: var(--ink); line-height: 18px; }
  .quote__author b { color: var(--quote-blue); font-weight: 700; }
  .back-mark {
    position: absolute; left: 385px; top: 178px; width: 114px; height: 114px; border-radius: 50%;
    background: var(--mark-fill);
  }
</style>
</head>
<body>

<section class="card card--front" aria-label="Card front">
  <div class="brand">
    <div class="brand__circle"></div>
    <span class="brand__name">ChoiceCraft</span>
  </div>

  <div class="identity">
    <p><span class="identity__name">Your Name,</span> <span class="identity__title">Title</span></p>
    <p class="identity__tagline">Supporting individual growth<br>and organizational development.</p>
  </div>

  <div class="divider"></div>

  <ul class="contact">
    <li>
      <svg viewBox="0 0 12 12" aria-hidden="true"><path d="M3 1 L5 3.5 L4 5 Q5 7 7 8 L8.5 7 L11 9 L9.5 11 Q5 11 2.5 8 Q0.5 5 1 2.5 Z"/></svg>
      123-456-789
    </li>
    <li>
      <svg viewBox="0 0 12 12" aria-hidden="true"><path d="M1 3 H11 V10 H1 Z M1.5 3.5 L6 7 L10.5 3.5" stroke="#fff" stroke-width="0.8"/></svg>
      info@choicecraftpro.net
    </li>
    <li><span class="social-square"></span>/choicecraftpro</li>
  </ul>

  <div class="band">
    <div class="band__light"></div>
    <div class="band__dark"></div>
    <span class="band__url">www.choicecraftpro.net</span>
  </div>
</section>

<section class="card card--back" aria-label="Card back">
  <ul class="quotes">
    <li class="quote">
      <span class="quote__dot"></span>
      <p class="quote__text">Try not to become a man of success, but rather a man of value.</p>
      <p class="quote__author">- <b>Arlen Whitcombe</b></p>
    </li>
    <li class="quote">
      <span class="quote__dot"></span>
      <p class="quote__text">The only constant is change.</p>
      <p class="quote__author">- <b>Thessaly Marr</b></p>
    </li>
    <li class="quote">
      <span class="quote__dot"></span>
      <p class="quote__text">We are what we repeatedly do. Excellence is not an act, it is a habit.</p>
      <p class="quote__author">- <b>Orestes Kalvin</b></p>
    </li>
    <li class="quote">
      <span class="quote__dot"></span>
      <p class="quote__text">Simplicity is the ultimate sophistication.</p>
      <p class="quote__author">- <b>Lucan DaVera</b></p>
    </li>
    <li class="quote">
      <span class="quote__dot"></span>
      <p class="quote__text">Life is not fair - get used to it.</p>
      <p class="quote__author">- <b>Benedict Gaile</b></p>
    </li>
  </ul>
  <div class="back-mark"></div>
</section>

</body>
</html>
```